Redesign of business card for Cedar Ridge Mechanical

We are looking for a new design for our business cards for Cedar Ridge Mechanical. We are a plumbing & HVAC construction company, operating on the West Coast of Canada and USA. Logo attached.
Industry/Entity Type
Construction - Plumbing & HVAC
Contact Information for Business Card
Name, address, phone numbers, email, website address
Look and feel
Each slider illustrates characteristics of the customer's brand and the style your logo design should communicate.

```html
<!DOCTYPE html>
<html lang="en">
<head>
<meta charset="utf-8">
<title>Cedar Ridge Mechanical – Business Card</title>
<link rel="stylesheet" href="https://fonts.googleapis.com/css2?family=Lato:wght@400;700&display=swap">
<style>
  :root {
    --page-bg: #d8d1c8;
    --card-bg: #e8e0d5;
    --ink: #1c1c1c;
    --ink-soft: #2a2a2a;
    --band: #0d0d0d;
    --band-light: #262626;
    --swoosh: #7a7570;
    --contact-text: #dccdb9;
    --icon: #c8b59c;
  }
  * { margin: 0; padding: 0; box-sizing: border-box; }
  html, body {
    width: 1200px;
    height: 1047px;
    overflow: hidden;
    background: var(--page-bg);
    font-family: "Lato", Arial, sans-serif;
  }
  .business-card {
    position: absolute;
    left: 100px;
    top: 243px;
    width: 1000px;
    height: 560px;
    border-radius: 22px;
    overflow: hidden;
    background: linear-gradient(160deg, #ece5db 0%, var(--card-bg) 60%, #ddd3c6 100%);
    box-shadow: 0 10px 30px rgba(0,0,0,0.18);
  }
  .card-band {
    position: absolute;
    inset: 0;
    width: 100%;
    height: 100%;
  }
  .brand {
    position: absolute;
    left: 52px;
    top: 120px;
    display: flex;
    align-items: center;
    gap: 18px;
  }
  .brand-square {
    width: 46px;
    height: 46px;
    background: var(--ink);
  }
  .brand-name {
    font-weight: 700;
    font-size: 36px;
    line-height: 1.15;
    letter-spacing: 1px;
    color: var(--ink);
    text-transform: uppercase;
  }
  .person {
    position: absolute;
    right: 34px;
    top: 118px;
    display: flex;
    align-items: stretch;
    gap: 12px;
  }
  .person-text { text-align: right; }
  .person-name {
    font-weight: 700;
    font-size: 36px;
    line-height: 1.05;
    color: var(--ink);
  }
  .person-title {
    font-size: 24px;
    color: var(--ink-soft);
    margin-top: 2px;
  }
  .person-bar {
    width: 17px;
    background: var(--ink);
  }
  .contact-list {
    position: absolute;
    left: 38px;
    top: 358px;
    list-style: none;
  }
  .contact-item {
    display: flex;
    align-items: center;
    gap: 9px;
    height: 38.5px;
    font-size: 25px;
    color: var(--contact-text);
  }
  .contact-icon {
    width: 22px;
    height: 22px;
    fill: var(--icon);
    flex: none;
  }
  .address {
    position: absolute;
    right: 34px;
    top: 428px;
    text-align: right;
    font-size: 25px;
    line-height: 38px;
    color: var(--contact-text);
  }
</style>
</head>
<body>
  <div class="business-card">
    <svg class="card-band" viewBox="0 0 1000 560" preserveAspectRatio="none" aria-hidden="true">
      <defs>
        <linearGradient id="band-fill" x1="0" y1="0" x2="1" y2="0">
          <stop offset="0" stop-color="var(--band-light)"/>
          <stop offset="0.5" stop-color="var(--band)"/>
          <stop offset="1" stop-color="var(--band)"/>
        </linearGradient>
        <linearGradient id="swoosh-fill" x1="0" y1="0" x2="1" y2="0">
          <stop offset="0" stop-color="#9c958d"/>
          <stop offset="0.6" stop-color="#6e6963"/>
          <stop offset="1" stop-color="#8d8780"/>
        </linearGradient>
      </defs>
      <path d="M0 312 Q520 292 1000 392 L1000 432 Q520 318 0 328 Z" fill="url(#swoosh-fill)"/>
      <path d="M0 334 Q520 316 1000 440 L1000 560 L0 560 Z" fill="url(#band-fill)"/>
    </svg>

    <div class="brand">
      <span class="brand-square"></span>
      <span class="brand-name">Cedar Ridge<br>Mechanical</span>
    </div>

    <div class="person">
      <div class="person-text">
        <div class="person-name">DANIEL HAYES</div>
        <div class="person-title">Managing Director</div>
      </div>
      <span class="person-bar"></span>
    </div>

    <ul class="contact-list">
      <li class="contact-item">
        <svg class="contact-icon" viewBox="0 0 24 24" aria-hidden="true"><path d="M6.6 10.8a15.1 15.1 0 0 0 6.6 6.6l2.2-2.2a1 1 0 0 1 1-.25 11.4 11.4 0 0 0 3.6.57 1 1 0 0 1 1 1V20a1 1 0 0 1-1 1A17 17 0 0 1 3 4a1 1 0 0 1 1-1h3.5a1 1 0 0 1 1 1c0 1.25.2 2.45.57 3.57a1 1 0 0 1-.25 1z"/></svg>
        123 456 789
      </li>
      <li class="contact-item">
        <svg class="contact-icon" viewBox="0 0 24 24" aria-hidden="true"><path d="M8 1h8a2 2 0 0 1 2 2v18a2 2 0 0 1-2 2H8a2 2 0 0 1-2-2V3a2 2 0 0 1 2-2zm0 3v14h8V4zm4 15.2a1 1 0 1 0 0 2 1 1 0 0 0 0-2z"/></svg>
        123 456 789
      </li>
      <li class="contact-item">
        <svg class="contact-icon" viewBox="0 0 24 24" aria-hidden="true"><path d="M2 6h20v13H2zm2 2v.4l8 5 8-5V8l-8 5z"/></svg>
        info@youremail.com
      </li>
      <li class="contact-item">
        <svg class="contact-icon" viewBox="0 0 24 24" aria-hidden="true"><path d="M12 2a10 10 0 1 0 0 20 10 10 0 0 0 0-20zm0 2a8 8 0 0 1 6.9 4H15l-1 2-3-1-2 2 1 3h2l1 3-1 3a8 8 0 0 1-1 .1A8 8 0 0 1 5 7.5L7 10l2-1 1-3-1-2z"/></svg>
        www.yourwebsite.com
      </li>
    </ul>

    <div class="address">
      Your address, City<br>
      State, Zip 1234
    </div>
  </div>
</body>
</html>
```